Brindle Children's Center - Child Care brochure

I just bought a new child care and completely renovated the space. We are also designing a new website, so I need the brochure to match that with updated info. www.brindlechildrenscenter.com - Information on there is current. We expect to have the new one up and running in the next few days. We have new photo's that I'd like to be added to the flyer too. ps. the boys in the pictures are mine, so i would appreciate one of them being added :). support@netcrafterhub.com has details on the website (dev.brindlechildrenscenter.com). The child care program is only open during the ski season - i.e. a resort facility catering to high end clients.
I'm attaching the the website information, the flyer I created, logo files and pictures.

Target Market(s)

Parents of young children

Font styles to use
Other font styles liked:
• "Things we said" & "Calibri Light"

Colors
cfeae6
fef1ee

Requirements
Must have
• Pictures of children. sleek design - winter, mountain theme. Check with website designer on new website.
Nice to have
• prices included
Should not have
• Kid like artwork

```html
<!DOCTYPE html>
<html lang="en">
<head>
<meta charset="utf-8">
<title>Brindle Children's Center – Brochure</title>
<link href="https://fonts.googleapis.com/css2?family=Carlito:ital,wght@0,400;0,700;1,700&family=Gochi+Hand&display=swap" rel="stylesheet">
<style>
  :root{
    --mint:#cfeae6;
    --blush:#fef1ee;
    --teal:#3a9d98;
    --teal-dark:#2f8a85;
    --salmon:#e0796c;
    --ink:#5a5a5a;
    --white:#ffffff;
  }
  *{box-sizing:border-box;margin:0;padding:0}
  html,body{width:1200px;height:932px;overflow:hidden;background:var(--white)}
  .brochure{position:relative;width:1200px;height:932px;overflow:hidden;background:var(--white);
    font-family:"Carlito",Calibri,sans-serif;color:var(--ink);font-size:14.6px;line-height:20px}
  .panel-left{position:absolute;left:0;top:0;width:402px;height:932px;background:var(--mint)}
  .panel-right{position:absolute;left:814px;top:300px;width:386px;height:632px;background:var(--blush)}
  .block{position:absolute}
  .script{font-family:"Gochi Hand",cursive;font-weight:400}
  .title{font-size:31px;line-height:34px;color:var(--teal)}
  .mission{font-weight:700;font-style:italic;color:var(--teal-dark);font-size:17.5px;line-height:22px;margin-top:12px}
  .heading-teal{font-size:25px;line-height:28px;color:var(--teal);margin-bottom:10px}
  .heading-salmon{font-size:21px;line-height:24px;color:var(--salmon);margin-bottom:6px}
  p{text-align:justify}
  p + p{margin-top:0}
  .link{color:var(--salmon)}
  .photo-band{position:absolute;left:0;top:0}
  .photo-circle{position:absolute;border-radius:50%;border:5px solid var(--white);
    box-shadow:0 2px 6px rgba(0,0,0,.18)}
  .photo-bottom{position:absolute;left:0;top:640px}
</style>
</head>
<body>
<main class="brochure">
  <div class="panel-left"></div>
  <div class="panel-right"></div>

  <svg class="photo-band" width="1200" height="340" viewBox="0 0 1200 340" role="img" aria-label="Photographs of young children playing with toys and on an interactive play floor">
    <defs>
      <linearGradient id="bandPhotoA" x1="0" y1="0" x2="1" y2="1">
        <stop offset="0" stop-color="#d9c9b8"/>
        <stop offset="1" stop-color="#9a8f86"/>
      </linearGradient>
      <linearGradient id="bandPhotoB" x1="0" y1="0" x2="0" y2="1">
        <stop offset="0" stop-color="#4e6b57"/>
        <stop offset="1" stop-color="#8fb86e"/>
      </linearGradient>
    </defs>
    <path d="M402 0 H800 V250 C700 236 560 246 402 300 Z" fill="url(#bandPhotoA)"/>
    <path d="M800 0 H1200 V300 C1080 262 940 246 800 250 Z" fill="url(#bandPhotoB)"/>
    <path d="M402 300 C560 246 700 236 800 250 C940 246 1080 262 1200 300 V318 C1080 282 930 266 800 270 C690 258 560 266 402 320 Z" fill="#ffffff"/>
  </svg>

  <div class="photo-circle" role="img" aria-label="Photograph of a smiling toddler in a yellow dress" style="left:626px;top:133px;width:126px;height:126px;background:radial-gradient(circle at 45% 40%,#e9c59a,#c48a52 70%,#8a6a4a)"></div>
  <div class="photo-circle" role="img" aria-label="Photograph of a baby in a blue dress playing on the floor" style="left:1022px;top:162px;width:134px;height:134px;background:radial-gradient(circle at 50% 40%,#e7d4c6,#7bb3bf 70%,#4f7f88)"></div>

  <svg class="photo-bottom" width="402" height="292" viewBox="0 0 402 292" role="img" aria-label="Photograph of a toddler reading a picture book beside a large teddy bear">
    <defs>
      <linearGradient id="readingPhoto" x1="0" y1="0" x2="1" y2="1">
        <stop offset="0" stop-color="#b79a72"/>
        <stop offset=".55" stop-color="#d8c1a4"/>
        <stop offset="1" stop-color="#8c7a66"/>
      </linearGradient>
    </defs>
    <path d="M0 16 C120 -6 280 -4 402 28 V292 H0 Z" fill="url(#readingPhoto)"/>
  </svg>

  <section class="block" style="left:26px;top:34px;width:352px">
    <h1 class="script title">Brindle Children's Center!</h1>
    <p class="mission">Our mission is to ensure that all children from across the globe feel safe, have fun and create magical vacation memories!</p>
    <p style="margin-top:16px">When you hit the slopes, you want to make sure your child has an enjoyable day too. At the Brindle Children's center, you can be sure that your child receives the best care possible – and has a great time to boot! Located on-site at the world-famous Brindle Ski Resort, you can drop off your child at a safe and fun care center and literally step out the door and hit the slopes.</p>
  </section>

  <section class="block" style="left:26px;top:356px;width:352px">
    <h2 class="script heading-teal">Our Services</h2>
    <p>The Brindle Children's Center is a full service child care facility that caters to children from 2 months old to 10 years old. Infants and young children can play, create and learn in the center. Children ages 4 and up can join Brindle's legendary Halvor Lund Ski School and spend the day learning from one of Brindle's friendly instructors. Our center is designed to stimulate curious young minds with areas set up for creative arts, social/emotional learning in the dramatic play area, blocks &amp; physical motor movement area, and a math and science discovery area. We provide 3 nutritious meals throughout the day.</p>
  </section>

  <section class="block" style="left:428px;top:308px;width:366px">
    <h2 class="script heading-teal">Our Staff</h2>
    <p>At the Brindle Children's Center, our staff take pride in creating a nurturing and creative atmosphere where your child can play, learn and grow. Each member of our staff team is trained in early childhood education, is certified in infant and child CPR and first aid. We work together as a team to provide the best care for children entrusted to us.</p>
    <p>Under the direction of Greta Holm, owner of Meadowlark Child Care, dba Brindle Children's Center, she ensures high quality because quite simply put, her passion is child care. She has her degree in Early Childhood Education, won the 2016 Early Childhood Teacher of the Year and is a 2017 National teacher award winner. Greta was born in South Africa to a German family and speaks English, Afrikaans and German fluently.</p>
  </section>

  <section class="block" style="left:428px;top:656px;width:366px">
    <h2 class="script heading-teal">Our Program</h2>
    <p>The Brindle Children's Center is fully licensed by the State Department of Health and offers a program that caters to your child's individual needs.</p>
  </section>

  <section class="block" style="left:428px;top:764px;width:366px">
    <h3 class="script heading-salmon">Infant care</h3>
    <p>Our infant care area is open from ages 2 months to walking toddlers. The area is safely enclosed to cater to the specific needs of an infant, with dim lightening, developmentally appropriate equipment and materials. The staff to children's ratio is low to provide the best care.</p>
  </section>

  <section class="block" style="left:828px;top:318px;width:358px">
    <h3 class="script heading-salmon">Young children</h3>
    <p>We know how to keep young minds busy. Your child will be giving opportunities to create art, play musical instruments, move, think and tinker that challenges their imagination.</p>
  </section>

  <section class="block" style="left:828px;top:436px;width:358px">
    <h3 class="script heading-salmon">Ski School</h3>
    <p>The Brindle Children's Center works closely with the famous Halvor Lund Ski School. If you wish to have your child participate in the group ski lesson (for ages 4 and up), The mini adventure package can be purchased at the ski school office and includes a half day at The Brindle Children's Center.</p>
  </section>

  <section class="block" style="left:828px;top:594px;width:358px">
    <h3 class="script heading-salmon">Après-ski care</h3>
    <p>After a fantastic day on the slopes, you can now enjoy social events or activities child free. We offer child care on Friday and Saturday evenings from 4:30 – 6:30PM. Don't forget to make reservations though at: <span class="link">reservations@brindlechildrenscenter.com</span></p>
  </section>

  <section class="block" style="left:828px;top:734px;width:358px">
    <h3 class="script heading-salmon">Need evening care?</h3>
    <p>Pick up a recommended babysitter list at the front desk. Professionals are at least 18 years old, CPR &amp; First Aid trained, background checked, and experience is listed on the sheet. Evening babysitters are not associated with the Brindle Children's Center after hours, and therefor need to be paid directly for services.</p>
  </section>
</main>
</body>
</html>
```